Event flyer for Sunday night Youth Group

Need a 4 x 6 or 5 x 7 flyer for a new youth group starting on April 14. The youth group is for students in middle school and high school so it needs to look fun and cool, but not childish. I prefer it not to include pictures of people unless it's so obscure you can't really see their faces. I've uploaded some pictures of flyers I like. I've also attached a couple versions of our logo to use on the flyer.
Information the flyer needs to include:
Youth Group
Sundays, 6-8pm (beginning April 14)
Location: Marlowe's - 4219 Quarry Fern Ave N, Keizer, 97318
There will be dinner, games, friends, and a message.
Target Market(s)
Youth ages 13-18
Industry/Entity Type
Church
Font styles to use
Colors
Designer to choose colors to be used in the design.
Look and feel

```html
<!DOCTYPE html>
<html lang="en">
<head>
<meta charset="utf-8">
<title>Youth Group Flyer</title>
<link href="https://fonts.googleapis.com/css2?family=Yellowtail&family=Oswald:wght@500&family=Open+Sans:wght@400;600;800&display=swap" rel="stylesheet">
<style>
  :root {
    --backdrop: #d3cbc6;
    --night: #1a0f22;
    --crowd-blue: #4a3fc4;
    --crowd-deep: #2a1f6e;
    --teal-base: #264653;
    --sky-blue: #29a8e0;
    --paper-white: #ffffff;
    --splash-grey: #c4c4c8;
    --ink: #161616;
    --band-purple: rgba(44, 20, 72, 0.88);
  }
  * { margin: 0; padding: 0; box-sizing: border-box; }
  html, body {
    width: 1200px; height: 1024px; overflow: hidden;
    background: var(--backdrop);
  }
  .flyer {
    position: absolute; left: 261px; top: 33px;
    width: 678px; height: 958px; overflow: hidden;
    background: var(--night);
  }
  .flyer__photo {
    position: absolute; inset: 0;
    background:
      radial-gradient(ellipse 260px 200px at 290px 300px, rgba(216,25,122,0.85), rgba(216,25,122,0) 70%),
      radial-gradient(ellipse 200px 160px at 560px 80px, rgba(140,40,170,0.6), rgba(140,40,170,0) 70%),
      linear-gradient(180deg, #1c0d1e 0%, #4a1747 22%, #3a2a9a 40%, var(--crowd-blue) 52%, var(--crowd-deep) 72%, #1a1430 84%, var(--teal-base) 92%, var(--teal-base) 100%);
  }
  .flyer__footer-fade {
    position: absolute; left: 0; right: 0; bottom: 0; height: 240px;
    background: linear-gradient(180deg, rgba(38,70,83,0) 0%, var(--teal-base) 40%, var(--teal-base) 100%);
  }
  .headline {
    position: absolute; left: 0; top: 0; width: 678px; height: 460px;
    overflow: visible;
  }
  .headline__youth, .headline__group {
    font-family: "Yellowtail", cursive;
  }
  .headline__youth { fill: var(--sky-blue); font-size: 220px; }
  .headline__group { fill: var(--paper-white); font-size: 96px; }
  .schedule-splash {
    position: absolute; left: 372px; top: 318px; width: 290px; height: 108px;
    transform: rotate(-4deg);
  }
  .schedule {
    position: absolute; left: 393px; top: 334px;
    transform: rotate(-4deg);
    font-family: "Oswald", sans-serif; font-weight: 500;
    color: var(--ink); font-size: 30px; line-height: 1.2;
    white-space: nowrap;
  }
  .venue-band {
    position: absolute; left: -20px; top: 472px; width: 720px; height: 58px;
    background: var(--band-purple);
    transform: rotate(3deg);
    display: flex; align-items: center; padding-left: 90px;
    font-family: "Open Sans", sans-serif; color: var(--paper-white);
    white-space: nowrap;
  }
  .venue-band__name { font-weight: 800; font-size: 28px; margin-right: 10px; }
  .venue-band__address { font-weight: 400; font-size: 19px; }
  .tagline {
    position: absolute; left: 0; right: 0; top: 790px; text-align: center;
    font-family: "Open Sans", sans-serif; font-weight: 400; font-size: 21px;
    color: var(--paper-white); white-space: nowrap;
  }
  .tagline__emphasis { font-weight: 800; letter-spacing: 2px; margin-left: 6px; }
  .church-mark {
    position: absolute; left: 0; right: 0; top: 850px;
    display: flex; align-items: center; justify-content: center; gap: 16px;
    font-family: "Open Sans", sans-serif;
  }
  .church-mark__square { width: 34px; height: 34px; background: var(--paper-white); }
  .church-mark__name {
    font-weight: 600; font-size: 28px; color: var(--paper-white);
    letter-spacing: 1px; white-space: nowrap;
  }
</style>
</head>
<body>
  <main class="flyer">
    <div class="flyer__photo" role="img" aria-label="Concert crowd under stage lights, pink glow over the stage and blue-lit audience"></div>
    <div class="flyer__footer-fade"></div>

    <svg class="headline" viewBox="0 0 678 460">
      <title>Youth Group</title>
      <text class="headline__youth" x="150" y="330" textLength="440" lengthAdjust="spacingAndGlyphs" transform="rotate(-14 150 330)">Youth</text>
      <text class="headline__group" x="318" y="330" textLength="215" lengthAdjust="spacingAndGlyphs" transform="rotate(-14 318 330)">Group</text>
    </svg>

    <svg class="schedule-splash" viewBox="0 0 290 108" aria-hidden="true">
      <path d="M14 22 C60 6 140 10 200 4 C240 0 276 8 286 30 C292 56 282 84 262 98 C210 108 120 104 60 102 C28 100 6 86 4 62 C2 44 4 30 14 22 Z" fill="var(--splash-grey)"/>
    </svg>
    <p class="schedule">Sundays, 6-8pm<br>(beginning April 14)</p>

    <div class="venue-band">
      <span class="venue-band__name">Marlowe's</span>
      <span class="venue-band__address">4219 Quarry Fern Ave N, Keizer, 97318</span>
    </div>

    <p class="tagline">There will be dinner, games, friends, and <span class="tagline__emphasis">a message</span></p>

    <div class="church-mark">
      <span class="church-mark__square"></span>
      <span class="church-mark__name">HARBOR LANE FELLOWSHIP</span>
    </div>
  </main>
</body>
</html>
```